Poster design for Belgian waffles

We are a local frozen yogurt chain that will introduce a new product for winter. It is Belgian waffle. You can have it a plain, with toppings such fresh fruit or with our frozen yogurt. We need two posters, one for introduction of the product and one that has pricing on it.

Target Market(s)

College students and young professionals

Industry/Entity Type

Pricing

```html
<!DOCTYPE html>
<html lang="en">
<head>
<meta charset="utf-8">
<title>Belgian Waffle Poster</title>
<link href="https://fonts.googleapis.com/css2?family=Source+Sans+3:wght@600;700&family=Nunito:wght@800&display=swap" rel="stylesheet">
<style>
  :root {
    --frame: #000000;
    --page: #ffffff;
    --panel-edge: #b4b4b4;
    --panel-mid: #eeeeee;
    --rule: #3a3a3a;
    --tab-top: #ff5a1e;
    --tab-bottom: #d42a0c;
    --headline: #5b7a2a;
    --waffle-text: #e27a16;
    --waffle-shade: #a8460a;
    --list-text: #8e8e8e;
    --bullet: #9a9a9a;
    --photo-light: #f3c16a;
    --photo-dark: #c9782a;
  }
  html, body {
    margin: 0;
    padding: 0;
    overflow: hidden;
  }
  .canvas {
    position: relative;
    width: 1200px;
    height: 1200px;
    box-sizing: border-box;
    background: var(--page);
    border: 10px solid var(--frame);
    overflow: hidden;
  }
  .poster {
    position: absolute;
    left: 178px;
    top: 46px;
    width: 839px;
    height: 1088px;
    background: linear-gradient(90deg, var(--panel-edge) 0%, var(--panel-mid) 45%, var(--panel-mid) 55%, var(--panel-edge) 100%);
    font-family: "Source Sans 3", "Myriad Pro", sans-serif;
    overflow: hidden;
  }
  .new-tab {
    position: absolute;
    left: 317px;
    top: 0;
    width: 191px;
    height: 71px;
    background: linear-gradient(180deg, var(--tab-top), var(--tab-bottom));
    border-radius: 0 0 8px 8px;
    color: #fff;
    font-weight: 700;
    font-size: 36px;
    line-height: 71px;
    text-align: center;
  }
  .headline {
    position: absolute;
    left: 0;
    right: 0;
    top: 112px;
    margin: 0;
    text-align: center;
    color: var(--headline);
    font-weight: 700;
    font-size: 53px;
    letter-spacing: 0.3px;
    line-height: 1;
  }
  .rule {
    position: absolute;
    left: 0;
    width: 100%;
    height: 2px;
    background: var(--rule);
  }
  .rule--top { top: 197px; }
  .rule--bottom { top: 755px; }
  .product-name {
    position: absolute;
    margin: 0;
    font-family: "Nunito", sans-serif;
    font-weight: 800;
    font-size: 130px;
    color: var(--waffle-text);
    text-shadow: 2px 2px 0 var(--waffle-shade);
    line-height: 1;
  }
  .product-name--first { left: 92px; top: 282px; }
  .product-name--second { left: 346px; top: 408px; }
  .product-photo {
    position: absolute;
    left: 70px;
    top: 430px;
    width: 276px;
    height: 144px;
    border-radius: 30px;
    background: radial-gradient(ellipse at 60% 45%, var(--photo-light), var(--photo-dark));
  }
  .brand-name {
    position: absolute;
    left: 244px;
    width: 504px;
    top: 588px;
    margin: 0;
    text-align: center;
    color: var(--headline);
    font-weight: 700;
    font-size: 60px;
    line-height: 1;
    white-space: nowrap;
  }
  .price-list {
    position: absolute;
    left: 100px;
    top: 793px;
    margin: 0;
    padding: 0;
    list-style: none;
  }
  .price-list li {
    display: flex;
    align-items: center;
    height: 59px;
    color: var(--list-text);
    font-weight: 600;
    font-size: 35px;
  }
  .price-list svg {
    width: 24px;
    height: 24px;
    margin-right: 34px;
    flex: none;
  }
</style>
</head>
<body>
<div class="canvas">
  <div class="poster">
    <div class="new-tab">NEW</div>
    <h1 class="headline">INTRODUCING THE DELICIOUS</h1>
    <div class="rule rule--top"></div>

    <div class="product-photo" role="img" aria-label="Photo of two Belgian waffles with a strawberry and blueberries"></div>
    <p class="product-name product-name--first">Belgian</p>
    <p class="product-name product-name--second">Waffle</p>
    <p class="brand-name">Snowdrift Yogurt</p>

    <div class="rule rule--bottom"></div>

    <ul class="price-list">
      <li><svg viewBox="0 0 24 24" aria-hidden="true"><circle cx="12" cy="12" r="11" fill="var(--bullet)"/><path d="M10 7l5 5-5 5" fill="none" stroke="#fff" stroke-width="3" stroke-linecap="round" stroke-linejoin="round"/></svg>Belgian Waffle with frozen yogurt $8</li>
      <li><svg viewBox="0 0 24 24" aria-hidden="true"><circle cx="12" cy="12" r="11" fill="var(--bullet)"/><path d="M10 7l5 5-5 5" fill="none" stroke="#fff" stroke-width="3" stroke-linecap="round" stroke-linejoin="round"/></svg>Belgian Waffle with frozen yogurt $8</li>
      <li><svg viewBox="0 0 24 24" aria-hidden="true"><circle cx="12" cy="12" r="11" fill="var(--bullet)"/><path d="M10 7l5 5-5 5" fill="none" stroke="#fff" stroke-width="3" stroke-linecap="round" stroke-linejoin="round"/></svg>Belgian Waffle with toppings $8</li>
      <li><svg viewBox="0 0 24 24" aria-hidden="true"><circle cx="12" cy="12" r="11" fill="var(--bullet)"/><path d="M10 7l5 5-5 5" fill="none" stroke="#fff" stroke-width="3" stroke-linecap="round" stroke-linejoin="round"/></svg>Waffle with frozen yogurt $8</li>
    </ul>
  </div>
</div>
</body>
</html>
```